Square V Dental Appointment Cards

This is a sister company of Tamarind Dental Group
We are a returning client.
This is what we like:
We like Parvell
Parvell font is cool
our Client is mostly Hispanic
We like to put Dr. Okafor, Orlith University Graduate
Please look at Tamarind Dental Appt. Cards/Business Cards
Updates

We would like to see new logos, too.

Industry/Entity Type

Dental

Contact Information for Business Card

Tobi R. Okafor, D.D.S
Orlith University Graduate
2836 West Larkspur Ave., Suite 410
Anaheim, CA 92817

Colors

Designer to choose colors to be used in the design.

Requirements
Nice to have
• Parvell Features

```html
<!DOCTYPE html>
<html lang="en">
<head>
<meta charset="utf-8">
<title>Square V Dental – Appointment Cards</title>
<link rel="stylesheet" href="https://fonts.googleapis.com/css2?family=Cinzel:wght@400;600&family=Lato:wght@400;700&display=swap">
<style>
  :root {
    --brand-blue: #1b75b3;
    --ink: #2b2b2b;
    --rule: #555555;
    --muted: #8a8a8a;
    --box: #777777;
    --card: #ffffff;
    --backdrop: #e7e6e4;
  }
  * { box-sizing: border-box; margin: 0; padding: 0; }
  html, body { width: 1200px; height: 844px; overflow: hidden; }
  body {
    background: var(--backdrop);
    font-family: "Lato", Arial, sans-serif;
    color: var(--ink);
    position: relative;
  }
  .card {
    position: absolute;
    top: 273px;
    width: 520px;
    height: 298px;
    background: var(--card);
    box-shadow: 0 6px 18px rgba(0,0,0,.18);
    overflow: hidden;
  }
  .card--front { left: 50px; }
  .card--back { left: 630px; }

  /* Front */
  .brand {
    position: absolute;
    top: 62px; right: 40px;
    display: flex; align-items: center; gap: 12px;
  }
  .brand__dot {
    width: 46px; height: 46px;
    border: 3px solid var(--brand-blue);
    border-radius: 50%;
    flex: none;
  }
  .brand__name {
    font-family: "Cinzel", Georgia, serif;
    font-weight: 400;
    font-size: 28px;
    color: var(--brand-blue);
    letter-spacing: .5px;
    white-space: nowrap;
  }
  .contact { position: absolute; left: 40px; right: 40px; top: 168px; }
  .contact__name {
    display: flex; align-items: center; gap: 10px;
    font-family: "Cinzel", Georgia, serif;
    font-weight: 600; font-size: 17px;
    color: var(--brand-blue);
    white-space: nowrap;
  }
  .contact__name::after {
    content: ""; flex: 1; height: 1px; background: var(--rule);
  }
  .contact__degree { font-size: 15px; margin-top: 2px; }
  .contact__phone {
    display: flex; align-items: center; gap: 7px;
    font-size: 15px; margin-top: 8px;
  }
  .contact__phone svg { width: 18px; height: 18px; flex: none; }
  .contact__address { font-size: 15px; line-height: 1.3; margin-top: 8px; }

  /* Back */
  .appt {
    position: absolute; left: 36px; right: 30px; top: 48px;
    font-size: 13px; letter-spacing: .3px; white-space: nowrap;
  }
  .appt__label { font-weight: 700; text-transform: uppercase; }
  .appt__blank { color: var(--muted); }
  .days {
    position: absolute; left: 36px; right: 30px; top: 100px;
    display: flex; justify-content: space-between;
    list-style: none; font-size: 12px;
  }
  .days li { display: flex; align-items: center; gap: 5px; }
  .days li::before {
    content: ""; width: 15px; height: 15px;
    border: 1.5px solid var(--box);
  }
  .notice {
    position: absolute; left: 0; right: 0; top: 148px;
    text-align: center; font-size: 12.5px; font-weight: 700;
  }
  .band {
    position: absolute; left: 0; right: 0; bottom: 0; height: 88px;
    background: var(--brand-blue);
    display: flex; align-items: center; justify-content: center;
    color: #fff; font-size: 13px; letter-spacing: 1.5px;
  }
</style>
</head>
<body>
  <section class="card card--front">
    <div class="brand">
      <span class="brand__dot"></span>
      <span class="brand__name">Square V Dental</span>
    </div>
    <div class="contact">
      <p class="contact__name">TOBI R. OKAFOR, D.D.S</p>
      <p class="contact__degree">Orlith University Graduate</p>
      <p class="contact__phone">
        <svg viewBox="0 0 20 20" aria-hidden="true">
          <circle cx="10" cy="10" r="8.5" fill="none" stroke="var(--brand-blue)" stroke-width="1.6"/>
          <path d="M7 5.5c-.8.4-1.3 1.2-1 2.4.8 2.8 2.9 4.9 5.6 5.9 1.1.4 2-.1 2.4-.9l-1.7-1.4-1.1.7c-1.2-.6-2.2-1.6-2.8-2.8l.7-1.1z" fill="var(--brand-blue)"/>
        </svg>
        000 222 0000
      </p>
      <p class="contact__address">2836 West Larkspur Ave.,<br>Suite 410 Anaheim, CA 92817</p>
    </div>
  </section>

  <section class="card card--back">
    <p class="appt">
      <span class="appt__label">Your next appointment</span>
      <span class="appt__blank">....................</span> at<span class="appt__blank">...............</span> am/pm
    </p>
    <ul class="days">
      <li>MON</li><li>TUE</li><li>WED</li><li>THU</li><li>FRI</li><li>SAT</li>
    </ul>
    <p class="notice">If unable to keep appointment, kindly give 24hrs notice.</p>
    <div class="band">www.websitename.com</div>
  </section>
</body>
</html>
```